Vibrant, yet professional, stationery set and other designs required.

I need to source a fantastic designer for a new project as part of my company using a new logo designed via sketch harbor.

**UPDATE** I am not looking for just 'fine' design that will suffice. I am looking for something great.

We are a life assurance brokerage based in Dublin, Ireland and BrightRoost.ie is our new website aimed at providing services for young families in Ireland. We are hoping to be the 'Velro' level of service providers in this area and I am looking for the quality of design to reflect this :-) Hopefully that makes sense!

I have a preference for straight lines over curves and waves.

I need...

1. Business card
2. Letterhead
3. Banner (for printing - 76cm X 305cm)
4. Car branding for KORVA 9 (2014 sport model) I believe the templates are freely available online.

Target Market(s)

Parents in Ireland - Aged 27 to 50.

Industry/Entity Type

Financial Planning

Colors

Designer to choose colors to be used in the design.

Requirements
Must have
• All of the items listed in the description above. I like clean, bright, legible, vibrant and professional design.
Should not have
• No silly or 'cheap' looking designs. This is a professional company looking to provide a professional service.

```html
<!DOCTYPE html>
<html lang="en">
<head>
<meta charset="utf-8">
<title>BrightRoost.ie — Business Card</title>
<link href="https://fonts.googleapis.com/css2?family=Roboto:wght@400;500&display=swap" rel="stylesheet">
<style>
  :root {
    --backdrop: #dddddd;
    --card-white: #f6f6f6;
    --card-slate: #8e9a9d;
    --brand-grey: #8a9598;
    --accent-green: #8dc63f;
    --text-dark: #4a4a4a;
    --text-mid: #8a9193;
    --white: #ffffff;
  }
  html, body {
    margin: 0;
    padding: 0;
    width: 1200px;
    height: 960px;
    overflow: hidden;
    background: var(--backdrop);
    font-family: "Roboto", Arial, sans-serif;
  }
  .canvas {
    position: relative;
    width: 1200px;
    height: 960px;
  }
  .card {
    position: absolute;
    width: 601px;
    height: 341px;
    box-sizing: border-box;
  }
  .card--front {
    left: 302px;
    top: 130px;
    background: var(--card-white);
  }
  .card--back {
    left: 299px;
    top: 489px;
    background: var(--card-slate);
  }
  .brand {
    position: absolute;
    left: 0;
    right: 0;
    display: flex;
    justify-content: center;
    align-items: center;
    gap: 12px;
    font-weight: 500;
    font-size: 50px;
    letter-spacing: -0.5px;
    line-height: 1;
  }
  .card--front .brand {
    top: 95px;
    color: var(--brand-grey);
  }
  .card--back .brand {
    top: 140px;
    color: var(--white);
  }
  .brand__dot {
    width: 16px;
    height: 16px;
    border-radius: 50%;
    background: var(--accent-green);
    flex: none;
  }
  .card--back .brand__dot {
    background: var(--white);
  }
  .contact {
    position: absolute;
    left: 0;
    right: 0;
    top: 205px;
    text-align: center;
    color: var(--text-dark);
  }
  .contact__name-line {
    margin: 0 0 4px;
    font-size: 15px;
    color: var(--text-mid);
    font-weight: 500;
  }
  .contact__name {
    font-size: 19px;
    color: var(--accent-green);
  }
  .contact__line {
    margin: 0 0 4px;
    font-size: 14px;
    font-weight: 400;
  }
  .contact__label {
    color: var(--accent-green);
    font-weight: 500;
  }
  .contact__web {
    margin: 0;
    font-size: 13px;
    letter-spacing: 2.4px;
    font-weight: 500;
  }
</style>
</head>
<body>
  <main class="canvas">
    <section class="card card--front" aria-label="Business card front">
      <div class="brand">
        <span class="brand__name">BrightRoost.ie</span>
        <span class="brand__dot" aria-hidden="true"></span>
      </div>
      <div class="contact">
        <p class="contact__name-line"><span class="contact__name">Liam Doyle -</span> CEO/Founder</p>
        <p class="contact__line">4120 Hollow Creek Road, Kenmore, Ohio 58213</p>
        <p class="contact__line"><span class="contact__label">P</span>: 614 502 7391 <span class="contact__label">E</span>: liam@brightroost.com</p>
        <p class="contact__web">www.brightroost.com</p>
      </div>
    </section>
    <section class="card card--back" aria-label="Business card back">
      <div class="brand">
        <span class="brand__name">BrightRoost.ie</span>
        <span class="brand__dot" aria-hidden="true"></span>
      </div>
    </section>
  </main>
</body>
</html>
```